Web design project for exciting Australian start-up

Background
We are looking for a creative and talented web design artist to work alongside our market leading web developer.
• You will be required to create a modern and clean design theme for our website, incorporating selected rustic colour scheme elements for our exciting Australian start-up to operate within the coffee industry.
reoccurring work to be expected to flow to the successful designer.
Requirements
• c. 5 - 10 page website
• Landing page
• Log in/ out
• 404 template
• Typography is emphasised
• Please use either a) typemarrow.com, b) free web fonts, c) brindle fonts
• All design elements in vector format
• Preferably with icons for each header title(i.e. about us, how it works etc) but designer have free reign over how the site looks, so might not be applicable
• All pages to be responsive
• Down to eSlab resolution

High level visual design brief attached - additional pages to be worked from base design.

Design inspiration
• We would like to use design elements from the following sources:
http://www.zandrix.com/halcyon/ (Functionality)
Colour scheme refer to logo and complementary style guide

```html
<!DOCTYPE html>
<html lang="en">
<head>
<meta charset="utf-8">
<title>Brew Meridian – Dashboard</title>
<link href="https://fonts.googleapis.com/css2?family=PT+Sans:wght@400;700&family=Arimo:wght@400&family=Oswald:wght@500&display=swap" rel="stylesheet">
<style>
:root{
  --bean-bg:#f5f0ec;
  --page:#ffffff;
  --caramel:#e0a866;
  --caramel-dark:#c98c47;
  --ink:#333333;
  --text:#555555;
  --charcoal:#3f3f3f;
  --panel-grey:#f3f3f3;
  --line:#bcbcbc;
  --footer:#dcdcdc;
  --footer-bar:#4d4d4d;
  --today:#2e3e9c;
}
*{box-sizing:border-box;margin:0;padding:0}
html,body{width:1200px;height:841px;overflow:hidden}
body{position:relative;background:var(--bean-bg);font-family:"PT Sans",sans-serif;color:var(--text)}
.abs{position:absolute}
.page{position:absolute;left:75px;top:0;width:1055px;height:634px;background:var(--page)}

/* header */
.brand{left:100px;top:52px;display:flex;align-items:center;gap:14px}
.brand-dot{width:52px;height:52px;border-radius:50%;background:var(--caramel)}
.brand-name{font:700 36px/1 "PT Sans",sans-serif;color:#111;letter-spacing:1px}
.btn{height:33px;border-radius:5px;color:#fff;display:flex;align-items:center;justify-content:center;box-shadow:0 1px 2px rgba(0,0,0,.35)}
.btn-dark{left:733px;top:60px;width:124px;background:linear-gradient(#6a6a6a,#2f2f2f);font-size:14px}
.btn-gold{top:60px;width:110px;background:linear-gradient(#e2ad6e,#c58a48);font:700 17px "PT Sans",sans-serif;letter-spacing:.5px}
.btn-login{left:868px}
.btn-signup{left:990px}
.header-rule{left:100px;top:131px;width:1000px;height:4px;background:var(--caramel)}

/* profile */
.profile-card{left:100px;top:152px;width:216px;height:181px;border:1px solid #cfcfcf;border-radius:8px;background:linear-gradient(#ffffff,#dcdcdc)}
.profile-photo{left:52px;top:5px;width:105px;height:105px;border-radius:50%;background:radial-gradient(circle at 45% 45%,#8a5a33,#3a2414)}
.profile-info{left:0;top:113px;width:214px;text-align:center;font-size:13px;line-height:20px;color:#444}

.account-head{left:100px;top:346px;width:216px;height:48px;border-radius:6px 6px 0 0;background:linear-gradient(#707070,#2f2f2f);color:#fff;font-size:20px;padding:14px 14px 0}
.account-body{left:100px;top:394px;width:216px;height:194px;border:1px solid #cfcfcf;border-top:none;padding:17px 13px;font-size:17px;line-height:24px;color:#444}
.account-body p{margin-bottom:11px}

/* tender */
.section-title{color:var(--caramel);font-size:22px;font-weight:400}
.tender-title{left:346px;top:148px;font-size:20px;letter-spacing:.3px}
.t-label{font-size:15px;font-weight:700;color:var(--ink)}
.t-value{font-size:15px;color:#555}
.t-olabel{font-size:15px;color:var(--caramel)}
.tile{width:30px;height:30px;border-radius:3px;background:linear-gradient(#3a3a3a,#111);color:#fff;font:500 20px/30px "Oswald",sans-serif;text-align:center;box-shadow:0 2px 3px rgba(0,0,0,.4)}
.tile-cap{width:30px;text-align:center;font-size:8px;color:#555}
.tender-rule{left:333px;top:336px;width:540px;height:2px;background:#8c8c8c}
.empty-box{width:527px;height:101px;background:var(--panel-grey);border:1px solid var(--line)}

/* tabs */
.tab-shape{position:absolute;left:0;top:0}
.tab-label{position:relative;display:block;color:#fff;font-weight:700;letter-spacing:.3px;text-shadow:0 1px 1px rgba(0,0,0,.5)}
.tab .tab-label{font-size:14px;line-height:32px;padding-left:38px}
.foot-tab .tab-label{font-size:16px;line-height:40px;padding-left:18px}

/* sidebar */
.side-links{left:893px;top:192px;font-size:13px;line-height:19px}
.side-links .on{color:var(--caramel)}
.side-links .off{color:#444}
.week{left:893px;top:243px;width:203px;height:170px;border:1px solid #cfcfcf;background:linear-gradient(#ffffff,#d6d6d6)}
.panel-head{height:35px;background:linear-gradient(#d9a163,#c28644);color:#fff;font-size:13px;display:flex;align-items:center;justify-content:space-between;padding:0 12px}
.event{position:absolute;left:8px;width:168px;font-size:11px;line-height:16px;color:#222}
.scroll-track{left:189px;top:45px;width:2px;height:118px;background:#555}
.scroll-thumb{left:184px;top:52px;width:12px;height:24px;border-radius:6px;background:linear-gradient(#e7b577,#c1833f)}
.calendar{left:893px;top:417px;width:204px;border:1px solid #cfcfcf}
.cal-grid{display:grid;grid-template-columns:repeat(7,1fr);gap:1px;background:#fff}
.cal-grid span{height:22px;font-size:9px;color:#fff;display:flex;align-items:center;justify-content:center;background:var(--caramel)}
.cal-grid .dow{background:#3c3c3c;font-weight:700}
.cal-grid .today{background:var(--today)}
.cal-grid .blank{grid-column:span 5}
.download{left:893px;top:601px;display:flex;align-items:center;gap:9px;font-size:13px;color:#444}

/* footer */
.footer{left:0;top:634px;width:1200px;height:167px;background:var(--footer);font-family:"Arimo",sans-serif}
.foot-tab{height:40px;width:150px}
.foot-list{font-size:14px;line-height:20px;color:#222;list-style:none}
.foot-list li{position:relative}
.foot-list li:first-child::before{content:"";position:absolute;left:-19px;top:5px;border:6px solid transparent;border-top:8px solid var(--caramel)}
.copyright{left:0;top:801px;width:1200px;height:40px;background:var(--footer-bar);color:#fff;font:14px/46px "Arimo",sans-serif;text-align:center}
</style>
</head>
<body>
<div class="page"></div>

<svg width="0" height="0" style="position:absolute">
  <defs>
    <linearGradient id="tab-grad" x1="0" y1="0" x2="0" y2="1"><stop offset="0" stop-color="#727272"/><stop offset="1" stop-color="#2c2c2c"/></linearGradient>
  </defs>
</svg>

<header>
  <div class="abs brand"><span class="brand-dot"></span><span class="brand-name">BREW MERIDIAN</span></div>
  <a class="abs btn btn-dark">Product portfolio</a>
  <a class="abs btn btn-gold btn-login">LOG IN</a>
  <a class="abs btn btn-gold btn-signup">SIGN UP</a>
  <div class="abs header-rule"></div>
</header>

<aside>
  <div class="abs profile-card">
    <div class="abs profile-photo" role="img" aria-label="Profile photo: mug made of coffee beans"></div>
    <svg class="abs" style="left:9px;top:98px" width="20" height="26"><path d="M17 2L5 13L17 24L14 13Z" fill="#d9a466"/></svg>
    <svg class="abs" style="left:184px;top:98px" width="20" height="26"><path d="M3 2L15 13L3 24L6 13Z" fill="#d9a466"/></svg>
    <div class="abs profile-info">Sam Sample Coffee Beans<br>Melbourne, Australia<br>Member since [Feb, 2014]</div>
  </div>
  <div class="abs account-head">MY ACCOUNT</div>
  <div class="abs account-body">
    <p>Email Address<br>Verified</p>
    <p>Circlepage<br>[x] Friends</p>
    <p>Overall feedback history<br>[x] No. of reviews</p>
  </div>
</aside>

<main>
  <h2 class="abs section-title tender-title">TENDER RESPONSES REQUIRED (#)</h2>
  <span class="abs t-label" style="left:347px;top:198px">Tender format</span>
  <span class="abs t-value" style="left:463px;top:198px">One-off</span>
  <span class="abs t-label" style="left:347px;top:230px">Machinery</span>
  <span class="abs t-value" style="left:462px;top:230px">[Commercial grade]</span>
  <span class="abs t-label" style="left:347px;top:260px">Barista training</span>
  <span class="abs t-value" style="left:466px;top:260px">3 staff</span>
  <span class="abs t-label" style="left:347px;top:294px">Accessories</span>
  <span class="abs t-value" style="left:462px;top:294px">[Cups, sugar]</span>
  <span class="abs t-olabel" style="left:637px;top:198px">Quantity (kg)</span>
  <span class="abs t-value" style="left:731px;top:198px">35 kg/week</span>
  <span class="abs t-olabel" style="left:636px;top:235px">Café type</span>
  <span class="abs t-value" style="left:715px;top:235px">Speciality coffee shop</span>
  <span class="abs t-olabel" style="left:637px;top:274px;line-height:18px">Countdown<br>timer</span>
  <div class="abs tile" style="left:734px;top:270px">44</div>
  <div class="abs tile" style="left:772px;top:270px">22</div>
  <div class="abs tile" style="left:809px;top:270px">27</div>
  <div class="abs tile-cap" style="left:734px;top:306px">DAYS</div>
  <div class="abs tile-cap" style="left:772px;top:306px">hours</div>
  <div class="abs tile-cap" style="left:809px;top:306px">mins</div>
  <svg class="abs" style="left:332px;top:311px" width="14" height="18"><path d="M12 1L3 9L12 17L10 9Z" fill="#d9a466"/></svg>
  <svg class="abs" style="left:859px;top:311px" width="14" height="18"><path d="M2 1L11 9L2 17L4 9Z" fill="#d9a466"/></svg>
  <div class="abs tender-rule"></div>

  <h2 class="abs section-title" style="left:346px;top:346px">Scheduled deliveries</h2>
  <div class="abs empty-box" style="left:342px;top:376px"></div>
  <h2 class="abs section-title" style="left:342px;top:487px">Recurring orders</h2>
  <div class="abs empty-box" style="left:341px;top:520px"></div>
</main>

<aside>
  <div class="abs tab" style="left:893px;top:153px;width:122px;height:32px">
    <svg class="tab-shape" width="122" height="32"><path d="M3 0H110L122 16L110 32H3Q0 32 0 29V3Q0 0 3 0Z" fill="url(#tab-grad)"/></svg>
    <span class="tab-label">INBOX</span>
  </div>
  <div class="abs side-links">
    <div class="on"><svg width="10" height="10"><path d="M7 1L2 5L7 9Z" fill="#e0a866"/></svg> Live tenders</div>
    <div class="off"><svg width="10" height="10"><path d="M0 2H10L5 8Z" fill="#444"/></svg> Messages</div>
  </div>

  <div class="abs week">
    <div class="panel-head"><span>‹</span><span>This week</span><span>›</span></div>
    <div class="event" style="top:40px">8 am – 11 am<br>Delivery of order 3220x<br>Order: 20kg Wonder Roast</div>
    <div class="abs" style="left:6px;top:97px;width:170px;height:1px;background:#bbb"></div>
    <div class="event" style="top:104px;left:11px">8 am – 11 am<br>Delivery of order 3220x<br>Order: 20kg Wonder Roast</div>
    <div class="abs scroll-track"></div>
    <div class="abs scroll-thumb"></div>
  </div>

  <div class="abs calendar">
    <div class="panel-head"><span>‹</span><span>February 2014</span><span>›</span></div>
    <div class="cal-grid">
      <span class="dow">M</span><span class="dow">T</span><span class="dow">W</span><span class="dow">T</span><span class="dow">F</span><span class="dow">S</span><span class="dow">S</span>
      <span>1</span><span>2</span><span>3</span><span>4</span><span>5</span><span>6</span><span>7</span>
      <span>8</span><span>9</span><span>10</span><span>11</span><span>12</span><span>13</span><span>14</span>
      <span>15</span><span>16</span><span>17</span><span>18</span><span>19</span><span class="today">20</span><span>21</span>
      <span>22</span><span>23</span><span>24</span><span>25</span><span>26</span><span>27</span><span>28</span>
      <span>29</span><span>30</span><span class="blank"></span>
    </div>
  </div>
  <div class="abs download">
    <svg width="18" height="18"><path d="M9 2V11M5 7L9 11L13 7" fill="none" stroke="#666" stroke-width="2"/><path d="M2 13V16H16V13" fill="none" stroke="#666" stroke-width="2"/></svg>Download
  </div>
</aside>

<footer>
  <div class="abs footer">
    <div class="abs foot-tab" style="left:119px;top:28px">
      <svg class="tab-shape" width="150" height="40"><path d="M4 0H136L150 20L136 40H4Q0 40 0 36V4Q0 0 4 0Z" fill="url(#tab-grad)"/></svg>
      <span class="tab-label">HELPFUL INFO</span>
    </div>
    <ul class="abs foot-list" style="left:145px;top:74px"><li>About us</li><li>Media enquiries</li><li>Terms &amp; conditions</li><li>Privacy policy</li></ul>

    <div class="abs foot-tab" style="left:316px;top:27px">
      <svg class="tab-shape" width="150" height="40"><path d="M4 0H136L150 20L136 40H4Q0 40 0 36V4Q0 0 4 0Z" fill="url(#tab-grad)"/></svg>
      <span class="tab-label" style="padding-left:21px">WHO WE ARE</span>
    </div>
    <ul class="abs foot-list" style="left:345px;top:73px"><li>How it works</li><li>FAQ</li><li>Contact us</li></ul>

    <div class="abs foot-tab" style="left:930px;top:27px">
      <svg class="tab-shape" width="150" height="40"><path d="M4 0H136L150 20L136 40H4Q0 40 0 36V4Q0 0 4 0Z" fill="url(#tab-grad)"/></svg>
      <span class="tab-label" style="padding-left:27px">JOIN US ON</span>
    </div>
    <ul class="abs foot-list" style="left:969px;top:75px"><li>Circlepage</li><li>Chirpline</li><li>Workweave</li><li>Vidstream</li></ul>
  </div>
  <div class="abs copyright">Copyright © 2014 Brew Meridian</div>
</footer>
</body>
</html>
```